Design Website Templates for Photographers for Lumera Inc. (trylumera.example)

Lumera Inc. is a generative website company for wedding photographers.
We are seeking new photography website design inspirations for the next template to be offered on our platform. The catch is you must use the same data for your designs. You also must use all of the data somewhere in the design. You cannot add new content besides the data available. If you wish to add any elements It will be hardcoded and must be universally fitting for many different photographers. We recommend not using any hardcoded test.
Don't be afraid to be creative! Although the most important element of a photographers website is the photos, we are looking for unique and out-of-the-box designs for the actual site as well.
Here is the User generated data available to you:
- 4 Hero Images Landscape, 4 Hero Images Portrait
- Tagline “destination photographer based in Maui, Hawaii”
- “About Photo” of the photographer
- “About” Biography Text
- The design can use up to 3 colors + background color and 2 fonts
- 9 Gallery images
- 3 Packages/services that include landscape/portrait images, a price, a title and text
- Testimonials made up of an image, text and text for the name of testimonial giver
See some examples of our current website designs attached. You can use any of the data you see in the designs.
Updates
We are looking for designs that are less feminine and are more neutral in color and fonts. Currently our templates are more oriented towards feminine photographers. We want to have designs that speak to diverse audiences. We thank everyone for submitting and are reviewing the designs.
Number of Pages Required
1 page
Look and feel
Each slider illustrates characteristics of the customer's brand and the style your logo design should communicate.

```html
<!DOCTYPE html>
<html lang="en">
<head>
<meta charset="utf-8">
<title>Lumera — Destination Photographer</title>
<link href="https://fonts.googleapis.com/css2?family=Lora:wght@400;500&family=Montserrat:wght@400;500;600&display=swap" rel="stylesheet">
<style>
:root{
  --bg:#f0eeeb;
  --ink:#1c1c1c;
  --muted:#6f6a64;
  --white:#ffffff;
  --black:#000000;
  --accent:#f6b800;
  --line:#2a2a2a;
  --serif:'Lora', Georgia, serif;
  --sans:'Montserrat', Arial, sans-serif;
}
*{margin:0;padding:0;box-sizing:border-box}
html,body{width:1200px;height:5263px;overflow:hidden}
body{position:relative;background:var(--bg);color:var(--ink);font-family:var(--serif)}
.photo{position:absolute}
.section-title{position:absolute;left:0;width:1200px;text-align:center;font-family:var(--serif);font-weight:400;font-size:37px;letter-spacing:1px;text-transform:uppercase;color:var(--ink)}
.body-text{font-family:var(--serif);font-size:13.2px;line-height:25.6px;color:var(--muted);text-align:justify}
.btn-outline{position:absolute;display:flex;align-items:center;justify-content:center;border:1.5px solid var(--line);font-family:var(--sans);font-size:11.5px;letter-spacing:.5px;color:var(--ink);text-transform:uppercase}

/* hero */
.hero{position:absolute;left:0;top:0;width:1200px;height:690px;overflow:hidden}
.hero-photo{inset:0;background:
  radial-gradient(ellipse 300px 260px at 470px 170px,#e7cdb5 0%,rgba(231,205,181,0) 70%),
  radial-gradient(ellipse 260px 380px at 760px 330px,#44474c 0%,rgba(68,71,76,0) 75%),
  radial-gradient(ellipse 260px 200px at 520px 560px,#e9e6e0 0%,rgba(233,230,224,0) 70%),
  linear-gradient(180deg,#b0a07c 0%,#8a7a58 45%,#4b4230 80%,#2f2a21 100%)}
.hero-shade{position:absolute;inset:0;background:rgba(0,0,0,.18)}
.nav{position:absolute;left:0;top:0;width:1200px;height:86px;background:rgba(0,0,0,.35)}
.brand{position:absolute;left:110px;top:20px;font-family:var(--sans);font-weight:500;font-size:36px;letter-spacing:3px;color:var(--white)}
.nav-links{position:absolute;left:401px;top:32px;display:flex;font-family:var(--sans);font-size:11.5px;color:var(--white)}
.nav-links span{margin-right:28px;position:relative}
.nav-links .active::after{content:"";position:absolute;left:0;right:0;top:45px;height:3px;background:var(--white)}
.nav-book{position:absolute;left:934px;top:20px;width:153px;height:40px;border:1.5px solid var(--white);color:var(--white);font-family:var(--sans);font-size:11.5px;display:flex;align-items:center;justify-content:center}
.tagline{position:absolute;left:0;top:356px;width:1200px;text-align:center;font-family:var(--serif);font-weight:400;font-size:37px;line-height:47px;color:var(--white)}
.thumb{position:absolute;top:592px;width:80px;height:52px;background:linear-gradient(135deg,#e8e1d4,#9a8a72 60%,#5d5140)}
.thumb.current{top:573px;width:124px;height:84px;border:3px solid var(--white)}

/* about */
.about-text{position:absolute;left:139px;top:846px;width:436px}
.about-photo{left:630px;top:855px;width:433px;height:333px;background:
  radial-gradient(ellipse 110px 150px at 200px 180px,#9c9a98 0%,rgba(156,154,152,0) 70%),
  radial-gradient(circle at 45% 35%,#4a4744,#151413 70%)}

/* biography */
.bio-band{position:absolute;left:0;top:1310px;width:1200px;height:131px;background:var(--black)}
.bio-band h2{position:absolute;left:0;top:42px;width:1200px;text-align:center;font-family:var(--serif);font-weight:400;font-size:37px;color:var(--white);text-transform:uppercase}
.frame{position:absolute;border:1.5px solid var(--line)}
.bio-photo{left:163px;top:1574px;width:337px;height:378px;background:
  radial-gradient(ellipse 150px 120px at 230px 120px,#a89480 0%,rgba(168,148,128,0) 70%),
  radial-gradient(ellipse at 55% 45%,#e6ddd2 0%,#eeebe6 55%,var(--bg) 75%)}
.bio-portrait{position:absolute;left:163px;top:1686px;width:268px;height:268px;border-radius:50%;border:6px solid var(--white);background:radial-gradient(ellipse 90px 120px at 50% 65%,#8e7a60 0%,rgba(142,122,96,0) 80%),linear-gradient(160deg,#c2bfba,#8a857e)}
.bio-text{position:absolute;left:564px;top:1590px;width:434px}

/* gallery */
.g{background:linear-gradient(160deg,#a89886,#4f4639)}
.g.warm{background:linear-gradient(180deg,#7f93ad 0%,#e8b086 40%,#c49070 60%,#8a7360 100%)}
.g.dusk{background:linear-gradient(180deg,#9c9da1 0%,#5e5650 55%,#1f1c1a 100%)}
.g.green{background:linear-gradient(160deg,#9aa374,#6d6448 60%,#3b3a30)}
.g.night{background:radial-gradient(circle at 50% 45%,#b07a3c,#2a1c12 75%)}
.g.sky{background:linear-gradient(180deg,#b8c0c6 0%,#a9a08e 50%,#7a6a4c 100%)}
.g.rose{background:linear-gradient(160deg,#c9b59e,#7a5c44 55%,#2a2624)}

/* packages */
.pkg{position:absolute;top:3391px;width:305px;text-align:center}
.pkg-photo{width:305px;height:358px}
.pkg h3{margin-top:20px;font-family:var(--serif);font-weight:400;font-size:22px;color:var(--ink)}
.pkg .price{margin-top:3px;font-family:var(--serif);font-size:22px;color:var(--ink)}
.pkg p{margin:6px auto 0;width:250px;font-family:var(--serif);font-size:12px;line-height:18px;color:var(--ink)}
.pkg .more{display:inline-block;margin-top:10px;font-family:var(--serif);font-size:13px;color:var(--ink);text-decoration:underline}

/* testimonials */
.testi-bg{left:0;top:4006px;width:1200px;height:634px;background:linear-gradient(180deg,#3a3a3a 0%,#4a4740 40%,#2a2925 70%,#1a1918 100%)}
.testi-bg::after{content:"";position:absolute;inset:0;background:rgba(0,0,0,.35)}
.testi-title{position:absolute;left:0;top:4094px;width:1200px;text-align:center;font-family:var(--serif);font-weight:400;font-size:37px;color:var(--white)}
.quote{position:absolute;top:4174px;height:262px;padding:26px 28px;color:var(--white)}
.quote p{position:relative;font-family:var(--serif);font-size:13.2px;line-height:25.6px;text-align:justify}
.quote .who{position:relative;margin-top:14px;font-family:var(--serif);font-size:20px}
.quote .who small{font-size:12px;margin-left:18px}
.quote svg{position:absolute;left:0;top:0}
.avatar{position:absolute;top:4458px;width:86px;height:86px;border-radius:50%;background:radial-gradient(ellipse 30px 40px at 50% 75%,#6b5a48 0%,rgba(107,90,72,0) 90%),linear-gradient(160deg,#e5e2dd,#9b958e)}

/* contact */
.field{position:absolute;border:1.5px solid #555;border-radius:3px;background:var(--white);font-family:var(--sans);font-size:12.5px;color:#777;padding:16px 20px}
.submit{position:absolute;left:482px;top:5010px;width:244px;height:47px;background:var(--accent);font-family:var(--sans);font-weight:600;font-size:12.5px;color:var(--ink);display:flex;align-items:center;justify-content:center}
.footer{position:absolute;left:0;top:5163px;width:1200px;height:100px;background:#232323;color:var(--white);font-family:Arial,sans-serif;font-size:12px;text-align:center;padding-top:42px}
</style>
</head>
<body>

<header class="hero">
  <div class="photo hero-photo" role="img" aria-label="Wedding couple embracing in a golden field"></div>
  <div class="hero-shade"></div>
  <nav class="nav">
    <div class="brand">LUMERA</div>
    <div class="nav-links">
      <span class="active">HOME</span><span>ABOUT</span><span>BLOG</span><span>TESTIMONIALS</span><span>PORTFOLIO</span><span>GET IN TOUCH</span>
    </div>
    <div class="nav-book">BOOK WITH ME</div>
  </nav>
  <h1 class="tagline">Destination Photographer<br>Based in Maui, Hawaii</h1>
  <div class="thumb" style="left:379px" role="img" aria-label="Hero slide thumbnail"></div>
  <div class="thumb current" style="left:485px" role="img" aria-label="Current hero slide thumbnail"></div>
  <div class="thumb" style="left:636px" role="img" aria-label="Hero slide thumbnail"></div>
  <div class="thumb" style="left:738px" role="img" aria-label="Hero slide thumbnail"></div>
</header>

<section>
  <h2 class="section-title" style="top:780px">About Photo</h2>
  <div class="about-text">
    <p class="body-text">Lorem ipsum dolor sit amet, consectetur adipiscing elit, sed do eiusmod tempor incididunt ut labore et dolore magna aliqua. Ut enim ad minim veniam, quis nostrud exercitation ullamco laboris nisi ut aliquip ex ea commodo consequat. Duis aute irure dolor in reprehenderit in voluptate velit esse cillum dolore eu fugiat nulla pariatur. Excepteur sint occaecat cupidatat non proident, sunt in culpa qui officia deserunt mollit anim id est laborum. Lorem ipsum dolor sit amet, consectetur adipiscing elit, sed do eiusmod tempor incididunt ut labore et dolore magna aliqua. Ut enim ad minim veniam, quis nostrud exercitation ullamco laboris nisi ut aliquip ex ea commodo consequat.</p>
  </div>
  <div class="btn-outline" style="left:139px;top:1147px;width:153px;height:39px">Learn More</div>
  <div class="photo about-photo" role="img" aria-label="Couple dancing in the rain at night"></div>
</section>

<section>
  <div class="bio-band"><h2>Our Biography</h2></div>
  <div class="frame" style="left:110px;top:1513px;width:961px;height:507px"></div>
  <div class="frame" style="left:129px;top:1529px;width:959px;height:507px"></div>
  <div class="photo bio-photo" role="img" aria-label="Couple kissing, soft white background"></div>
  <div class="bio-portrait" role="img" aria-label="Portrait of the photographer"></div>
  <div class="bio-text">
    <p class="body-text">Lorem ipsum dolor sit amet, consectetur adipiscing elit, sed do eiusmod tempor incididunt ut labore et dolore magna aliqua. Ut enim ad minim veniam, quis nostrud exercitation ullamco laboris nisi ut aliquip ex ea commodo consequat. Duis aute irure dolor in reprehenderit in voluptate velit esse cillum dolore eu fugiat nulla pariatur. Excepteur sint occaecat cupidatat non proident, sunt in culpa qui officia deserunt mollit anim id est laborum. Lorem ipsum dolor sit amet, consectetur adipiscing elit, sed do eiusmod tempor incididunt ut labore et dolore magna aliqua. Ut enim ad minim veniam, quis nostrud exercitation ullamco laboris nisi ut aliquip ex ea commodo consequat.</p>
  </div>
  <div class="btn-outline" style="left:564px;top:1893px;width:152px;height:39px">Learn More</div>
</section>

<section aria-label="Gallery">
  <div class="photo g warm" style="left:8px;top:2146px;width:380px;height:262px" role="img" aria-label="Couple walking on a beach at sunset"></div>
  <div class="photo g green" style="left:409px;top:2146px;width:380px;height:262px" role="img" aria-label="Couple under falling petals with guests"></div>
  <div class="photo g dusk" style="left:809px;top:2146px;width:383px;height:262px" role="img" aria-label="Couple holding hands at dusk"></div>
  <div class="photo g rose" style="left:8px;top:2428px;width:380px;height:501px" role="img" aria-label="Groom kissing bride's forehead"></div>
  <div class="photo g green" style="left:409px;top:2428px;width:380px;height:266px" role="img" aria-label="Couple celebrating with confetti"></div>
  <div class="photo g sky" style="left:809px;top:2428px;width:383px;height:501px" role="img" aria-label="Groom lifting bride in a field"></div>
  <div class="photo g night" style="left:8px;top:2950px;width:380px;height:263px" role="img" aria-label="Couple with sparklers at night"></div>
  <div class="photo g rose" style="left:409px;top:2715px;width:380px;height:498px" role="img" aria-label="Close portrait of a couple with flower crown"></div>
  <div class="photo g" style="left:809px;top:2950px;width:383px;height:263px" role="img" aria-label="Bride with bouquet embracing groom"></div>
</section>

<section>
  <h2 class="section-title" style="top:3308px">Featured Packages</h2>
  <div class="pkg" style="left:110px">
    <div class="pkg-photo" style="background:linear-gradient(180deg,#b9bcae 0%,#8d8a72 50%,#6b6a52 100%)" role="img" aria-label="Couple walking through a meadow"></div>
    <h3>Wedding Collection</h3><div class="price">$55.00</div>
    <p>Lorem ipsum dolor sit amet, consectetur adipiscing elit, sed do eiusmod</p>
    <span class="more">More Info</span>
  </div>
  <div class="pkg" style="left:448px">
    <div class="pkg-photo" style="background:linear-gradient(160deg,#e6dccb 0%,#b49b7e 50%,#3b3632 100%)" role="img" aria-label="Couple embracing in soft light"></div>
    <h3>Wedding Collection</h3><div class="price">$65.00</div>
    <p>Lorem ipsum dolor sit amet, consectetur adipiscing elit, sed do eiusmod</p>
    <span class="more">More Info</span>
  </div>
  <div class="pkg" style="left:783px">
    <div class="pkg-photo" style="background:linear-gradient(160deg,#e2dfda 0%,#9c948a 50%,#3e3a36 100%)" role="img" aria-label="Couple against a white brick wall"></div>
    <h3>Wedding Collection</h3><div class="price">$75.00</div>
    <p>Lorem ipsum dolor sit amet, consectetur adipiscing elit, sed do eiusmod</p>
    <span class="more">More Info</span>
  </div>
</section>

<section>
  <div class="photo testi-bg" role="img" aria-label="Couple silhouetted on a hillside at dusk"></div>
  <h2 class="testi-title">TESTIMONIALS</h2>
  <div class="quote" style="left:110px;width:458px">
    <svg width="460" height="330" viewBox="0 0 460 330"><path d="M1 1H457V261H105L105 323L55 261H1Z" fill="none" stroke="#fff" stroke-width="2"/></svg>
    <p>Lorem ipsum dolor sit amet, consectetur adipiscing elit, sed do eiusmod tempor incididunt ut labore et dolore magna aliqua. Ut enim ad minim veniam, quis nostrud exercitation ullamco laboris nisi ut aliquip ex ea commodo consequat. Duis aute irure dolor in reprehenderit in voluptate velit esse cillum dolore eu fugiat nulla pariatur.</p>
    <div class="who">John doe<small>Company name</small></div>
  </div>
  <div class="avatar" style="left:229px" role="img" aria-label="Client portrait"></div>
  <div class="quote" style="left:619px;width:466px">
    <svg width="470" height="330" viewBox="0 0 470 330"><path d="M1 1H465V261H105L105 323L55 261H1Z" fill="none" stroke="#fff" stroke-width="2"/></svg>
    <p>Lorem ipsum dolor sit amet, consectetur adipiscing elit, sed do eiusmod tempor incididunt ut labore et dolore magna aliqua. Ut enim ad minim veniam, quis nostrud exercitation ullamco laboris nisi ut aliquip ex ea commodo consequat. Duis aute irure dolor in reprehenderit in voluptate velit esse cillum dolore eu fugiat nulla pariatur.</p>
    <div class="who">John doe<small>Company name</small></div>
  </div>
  <div class="avatar" style="left:736px" role="img" aria-label="Client portrait"></div>
</section>

<section>
  <h2 class="section-title" style="top:4735px">Lets Connect</h2>
  <div class="field" style="left:221px;top:4810px;width:245px;height:51px">Name</div>
  <div class="field" style="left:480px;top:4810px;width:246px;height:51px">Email</div>
  <div class="field" style="left:740px;top:4810px;width:249px;height:51px">Phone</div>
  <div class="field" style="left:221px;top:4879px;width:768px;height:119px">Text here..</div>
  <div class="submit">SUBMIT NOW</div>
</section>

<footer class="footer">© Copyrights 2023 The Company Name | All Rights Reserved</footer>

</body>
</html>
```